Letterhead, stationery and email signature for construction business

I need the letterhead, stationery and email signature designs for a construction business. I want them to have a corporate feel to them.

I've attached the logo for reference.

```html
<!DOCTYPE html>
<html lang="en">
<head>
<meta charset="utf-8">
<title>Halden Build Letterhead</title>
<link href="https://fonts.googleapis.com/css2?family=Lato:wght@400;700;900&family=Open+Sans:wght@400&family=Italianno&display=swap" rel="stylesheet">
<style>
  :root{
    --bg:#e2e2e2;
    --paper:#ffffff;
    --brand-blue:#2f55a4;
    --rule-blue:#2a6cc0;
    --slate:#4f4f5b;
    --ink:#1c1c1c;
    --contact:#3a3a3a;
  }
  *{margin:0;padding:0;box-sizing:border-box}
  html,body{width:1200px;height:1141px;overflow:hidden;background:var(--bg)}
  .letterhead{
    position:absolute;left:331px;top:84px;width:677px;height:957px;
    background:var(--paper);
    box-shadow:0 2px 10px rgba(0,0,0,.18);
    font-family:'Lato',sans-serif;color:var(--ink);overflow:hidden;
  }
  .brand{position:absolute;left:34px;top:64px;display:flex;align-items:center;gap:10px}
  .brand-mark{width:32px;height:32px;background:var(--brand-blue)}
  .brand-name{font-family:'Lato',sans-serif;font-weight:900;font-size:38px;color:var(--brand-blue);letter-spacing:.5px}
  .divider{position:absolute;left:444px;top:40px;width:2px;height:96px;background:var(--rule-blue)}
  .contact{position:absolute;left:469px;top:34px;font-family:'Open Sans',sans-serif;font-style:normal;font-size:15px;color:var(--contact);line-height:19.5px}
  .contact .address{margin-bottom:6px}
  .contact .line{display:flex;align-items:center;gap:5px}
  .contact svg{width:11px;height:11px;fill:var(--rule-blue)}
  .letter{position:absolute;left:34px;top:218px;width:610px;font-size:14px;line-height:16px}
  .date{margin-bottom:17px}
  .recipient{margin-bottom:15px}
  .company{margin-bottom:22px}
  .salutation{font-weight:700;font-size:17px;margin-bottom:20px}
  .body p{text-align:justify;font-size:13.6px;line-height:15px;margin-bottom:15px}
  .closing{margin-top:33px}
  .signature{font-family:'Italianno',cursive;font-size:42px;line-height:42px;margin-top:80px}
  .footer-rule{position:absolute;left:0;bottom:54px;width:677px;height:5px;background:var(--brand-blue)}
  .footer-band{position:absolute;left:0;bottom:0;width:677px;height:50px;background:var(--slate)}
</style>
</head>
<body>
<main class="letterhead">
  <header>
    <div class="brand">
      <span class="brand-mark"></span>
      <span class="brand-name">HALDEN BUILD</span>
    </div>
    <div class="divider"></div>
    <address class="contact">
      <div class="address">Your address, City<br>State, Zip 1234</div>
      <div class="line"><svg viewBox="0 0 12 12"><path d="M1 4c0-2 10-2 10 0v1H8V4H4v1H1z M2 6h8l1 5H1z"/></svg>123 456 789</div>
      <div class="line"><svg viewBox="0 0 12 12"><path d="M1 3h10v6H1z"/></svg>info@yourmail.com</div>
      <div class="line"><svg viewBox="0 0 12 12"><circle cx="6" cy="6" r="5"/></svg>www.yourwebsite.com</div>
    </address>
  </header>

  <section class="letter">
    <p class="date">January-03-2020</p>
    <p class="recipient">Mr, Peter Lane<br>President</p>
    <p class="company">Northway Corporation<br>123 Street Name, Suite# 10<br>City, State, 120023</p>
    <p class="salutation">Dear Mr, Peter</p>
    <div class="body">
      <p>Lorem ipsum dolor sit amet, consectetur adipiscing elit, sed do eiusmod tempor incididunt ut labore et dolore magna aliqua. Ut enim ad minim veniam, quis nostrud exercitation ullamco laboris nisi ut aliquip ex ea commodo consequat. Duis aute irure dolor in reprehenderit in voluptate velit esse cillum dolore eu fugiat nulla pariatur.</p>
      <p>Lorem ipsum dolor sit amet, consectetur adipiscing elit, sed do eiusmod tempor incididunt ut labore et dolore magna aliqua. Ut enim ad minim veniam, quis nostrud exercitation ullamco laboris nisi ut aliquip ex ea commodo consequat. Duis aute irure dolor in reprehenderit in voluptate velit esse cillum dolore eu fugiat nulla pariatur.</p>
      <p>Lorem ipsum dolor sit amet, consectetur adipiscing elit, sed do eiusmod tempor incididunt ut labore et dolore magna aliqua. Ut enim ad minim veniam, quis nostrud exercitation ullamco laboris nisi ut aliquip ex ea commodo consequat.</p>
      <p>Excepteur sint occaecat cupidatat non proident, sunt in culpa qui officia deserunt mollit anim id est laborum. re et dolore magnam aliquam quaerat voluptatem.</p>
    </div>
    <p class="closing">Regards</p>
    <p class="signature">Daniel Reed</p>
  </section>

  <footer>
    <div class="footer-rule"></div>
    <div class="footer-band"></div>
  </footer>
</main>
</body>
</html>
```